Web site for radio show

I've got a radio show starting on OrbitalWave and need a web site for it. I am familiar with WordPress, so I'd like to get a design for a WordPress-based web site for the show.

I'm also posting a logo project to be done at the same time.

The best radio show web site I've seen is the Cosmic Tuesday site (www.cosmictuesday-example.com). That's a good model but I don't want to start with that much complexity and content. The initial site that I'd like you to design would have the following parts:
- Upcoming shows
- Past shows (including links to authors, their web sites, and their books)
- Bird feed feed
- Blog
- About
- ...and anything else you think would be necessary

For colors, I'd like it to be consistent with my personal web site: www.kellaway-ventures-example.com

Target Market(s)

The target market for this show is mid- to upper-level managers

Industry/Entity Type

Radio

Requirements
Must have
• The project has to proceed in (at least) two stages: a first rough layout, and a second finished design. Whether you want a third stage in between with look and feel options is up to you.

```html
<!DOCTYPE html>
<html lang="en">
<head>
<meta charset="utf-8">
<title>Kellaway Show</title>
<link href="https://fonts.googleapis.com/css2?family=Open+Sans:wght@400;600;700&display=swap" rel="stylesheet">
<style>
:root{
  --page-bg:#f1f1f1;
  --panel:#ffffff;
  --red:#c8161d;
  --red-dark:#a30f15;
  --ink:#333333;
  --ink-soft:#666666;
  --ink-muted:#8a8a8a;
  --line:#d9d9d9;
  --sky:#1ba1e2;
  --sky-dark:#0f8fd0;
  --slider:#0b0b0b;
  --btn:#e4e4e4;
  --social:#444444;
}
*{margin:0;padding:0;box-sizing:border-box}
html,body{width:758px;height:1200px;overflow:hidden}
body{background:var(--page-bg);font-family:"Open Sans",Arial,sans-serif;color:var(--ink);position:relative}
.abs{position:absolute}
.page{left:71px;top:0;width:619px;height:1034px;background:var(--panel);box-shadow:0 2px 6px rgba(0,0,0,.15)}
.site-title{left:88px;top:13px;font-size:23px;font-weight:400;color:#555}
.site-title span{color:var(--red)}
.social-top{left:538px;top:6px;display:flex;gap:8px}
.social-top i{display:block;width:16px;height:16px;border-radius:2px}
.search{left:491px;top:36px;width:192px;height:15px;border:1px solid var(--line);display:flex}
.search .field{flex:1;font-size:6.5px;color:#aaa;padding:3px 0 0 13px}
.search .go{width:40px;background:var(--red);color:#fff;font-size:6.5px;text-align:center;padding-top:3px}
.nav{left:74px;top:64px;width:616px;height:29px;background:linear-gradient(#fff,#f0f0f0);border-top:1px solid var(--line);border-bottom:1px solid var(--line)}
.nav-item{top:64px;height:29px;font-size:8.5px;color:#222;line-height:29px}
.nav-home{left:77px;top:61px;width:59px;height:34px;background:linear-gradient(var(--red),var(--red-dark));color:#fff;font-size:8.5px;text-align:center;line-height:34px;border-radius:2px 2px 0 0;box-shadow:0 2px 3px rgba(0,0,0,.3)}
.nav-sep{top:66px;width:1px;height:26px;background:var(--line)}
.slider{left:82px;top:105px;width:595px;height:236px;background:var(--slider);border:2px solid #ddd;border-radius:4px;overflow:hidden}
.slider-photo{left:0;top:0;width:265px;height:232px;background:linear-gradient(135deg,#3a2a20,#6b4b36 45%,#1a120d)}
.slide-title{right:129px;top:150px;font-size:16px;color:#fff;letter-spacing:.3px}
.slide-rule{left:410px;top:172px;width:219px;height:1px;background:#777}
.slide-sub{right:129px;top:180px;font-size:11.5px;color:#fff}
.slide-text{left:410px;top:204px;width:219px;font-size:7.5px;line-height:13.3px;color:#ddd;text-align:right}
.slide-more{left:579px;top:274px;width:47px;height:20px;background:#8a8a8a;color:#fff;font-size:7.5px;text-align:center;line-height:20px}
.dots{left:579px;top:323px;display:flex;gap:5px}
.dots i{width:5px;height:5px;border-radius:50%;background:#aaa;display:block}
.dots i.on{background:var(--red)}
.h2{font-size:15px;color:#666;font-weight:400}
.h2 b{font-weight:400;color:#333}
.dotted{height:0;border-top:1px dotted #999}
.more{font-size:7.5px;color:var(--red)}
.arrow-dot{width:11px;height:11px;border-radius:50%;background:#555}
.arrow-dot::after{content:"";position:absolute;left:4px;top:3px;border-left:4px solid #fff;border-top:2.5px solid transparent;border-bottom:2.5px solid transparent}
.welcome-lead{left:84px;top:388px;font-size:8.8px;color:#222}
.body-text{font-size:7.3px;line-height:11.4px;color:#666}
.side-box{left:506px;top:360px;width:170px;height:364px;border:1px solid var(--line);border-radius:3px;box-shadow:0 1px 3px rgba(0,0,0,.1)}
.side-head{left:507px;top:361px;width:168px;height:22px;background:linear-gradient(#fff,#eee);font-size:11px;color:#777;padding:4px 0 0 6px}
.side-head b{font-weight:600;color:#444}
.show-img{width:154px;height:67px}
.show-title{font-size:9.6px;color:#222}
.show-text{font-size:7.1px;line-height:11.4px;color:#666;width:150px}
.book{width:76px;height:98px}
.past-text{font-size:7.8px;line-height:11.3px;color:#666;width:96px;overflow-wrap:anywhere;word-break:break-all}
.past-text .lead{word-break:normal;overflow-wrap:normal}
.past-btn{width:46px;height:20px;background:var(--btn);border:1px solid #ccc;border-radius:2px;font-size:7px;color:var(--red);text-align:center;line-height:18px}
.blog-img{width:149px;height:86px}
.blog-title{font-size:8.3px;line-height:13.6px;color:#222;width:226px}
.blog-by{font-size:7px;color:var(--ink-muted)}
.blog-text{font-size:7px;line-height:10.4px;color:#666;width:240px}
.share-btn{height:12px;font-size:6px;color:#fff;line-height:12px;padding-left:6px;border-radius:2px;font-weight:600}
.share-count{height:12px;border:1px solid #ccc;font-size:6.3px;color:#333;text-align:center;line-height:10px;background:#fff}
.tweet-box{left:506px;top:746px;width:170px;height:256px;border:1px solid var(--line);background:#fff}
.tweet-head{left:506px;top:746px;width:170px;height:24px;background:var(--sky);color:#fff;font-size:12.5px;padding:3px 0 0 36px}
.tweet-head i{position:absolute;left:9px;top:5px;width:14px;height:14px;border-radius:50%;background:#fff}
.follow{left:512px;top:778px;width:104px;height:12px;border:1px solid #ccc;border-radius:2px;background:linear-gradient(#fff,#eee);font-size:6.8px;line-height:10px;padding-left:14px;color:#333}
.follow::before{content:"";position:absolute;left:3px;top:2px;width:7px;height:7px;border-radius:50%;background:var(--sky)}
.followers{left:620px;top:778px;width:52px;height:12px;border:1px solid #ccc;font-size:6.3px;line-height:10px;text-align:center;color:#333}
.avatar{left:512px;width:30px;height:30px}
.tweet{left:550px;width:124px;font-size:7.1px;line-height:11.4px;color:#333;overflow-wrap:anywhere}
.tweet a{color:var(--sky-dark);text-decoration:none}
.view-all{left:507px;top:986px;width:168px;height:16px;background:var(--sky);color:#fff;font-size:8px;text-align:center;line-height:16px}
.foot-brand{left:68px;top:1060px;display:flex;align-items:center;gap:8px;font-size:27px;font-weight:700;color:#1f4fa0}
.foot-brand i{display:block;width:14px;height:14px;border-radius:50%;background:#1f4fa0}
.foot-social{left:514px;top:1065px;display:flex;gap:6.5px}
.foot-social i{display:block;width:24px;height:24px;border-radius:50%;background:var(--social)}
.foot-text{right:69px;font-size:7.2px;color:#333;text-align:right}
</style>
</head>
<body>
<div class="abs page"></div>

<header>
  <div class="abs site-title">Kellaway <span>Show</span></div>
  <div class="abs social-top">
    <i style="background:#3b5998"></i><i style="background:#dd4b39"></i><i style="background:#333"></i><i style="background:#f26522"></i><i style="background:#ff5500"></i><i style="background:#1da1f2"></i>
  </div>
  <div class="abs search"><div class="field">Enter Key word</div><div class="go">SEARCH</div></div>
</header>

<nav>
  <div class="abs nav"></div>
  <div class="abs nav-sep" style="left:234px"></div>
  <div class="abs nav-sep" style="left:316px"></div>
  <div class="abs nav-sep" style="left:382px"></div>
  <div class="abs nav-sep" style="left:456px"></div>
  <div class="abs nav-home">Home</div>
  <div class="abs nav-item" style="left:168px">About Us</div>
  <div class="abs nav-item" style="left:256px">Services</div>
  <div class="abs nav-item" style="left:339px">Blog</div>
  <div class="abs nav-item" style="left:405px">Shows</div>
  <div class="abs nav-item" style="left:481px">Contact Us</div>
</nav>

<section class="abs slider">
  <div class="abs slider-photo" role="img" aria-label="Host speaking with a headset microphone"></div>
</section>
<div class="abs slide-title">MAECENAS LOBORTIS LACUS.</div>
<div class="abs slide-rule"></div>
<div class="abs slide-sub">Curabitur Sapien Enim</div>
<div class="abs slide-text">Sed ut perspiciatis unde omnis iste natus error sit voluptatem accusantium doloremque laudantium, toram rem aperiam, eaque ipsa quae ab illo inventore veritatis et quasi architecto beatae vitae explicabo.</div>
<div class="abs slide-more">More</div>
<div class="abs dots"><i></i><i></i><i class="on"></i><i></i><i></i></div>

<section class="welcome">
  <div class="abs h2" style="left:84px;top:359px">Welcome to <b>Kellaway Show</b></div>
  <div class="abs dotted" style="left:84px;top:384px;width:354px"></div>
  <div class="abs welcome-lead">Mauris vel lacus vitae felis vestibulum volutpat. Etiam est nunc, venisl.</div>
  <p class="abs body-text" style="left:84px;top:408px;width:402px">Sed ut perspiciatis unde omnis iste natus error sit voluptatem accusantium doloremque laudantium, totam rem aperiam, eaque ipsa quae ab illo inventore veritatis et quasi architecto beatae vitae dicta sunt explicabo. Nemo enim ipsam voluptatem quia voluptas sit aspernatur aut odit aut fugit, sed quia consequuntur magni dolores eos qui ratione voluptatem sequi nesciunt. Neque porro quisquam est, qui dolorem ipsum quia dolor sit amet.Sed ut perspiciatis unde omnis iste natus error sit voluptatem accusantium doloremque laudantium, totam rem aperiam, eaque ipsa quae ab illo inventore veritatis et quasi architecto beatae vitae dicta sunt explicabo. Nemo enim ipsam voluptatem quia voluptas</p>
  <div class="abs more" style="left:457px;top:494px">More &gt;&gt;</div>
</section>

<aside>
  <div class="abs side-box"></div>
  <div class="abs side-head">Upcoming <b>Shows</b></div>
  <div class="abs show-img" style="left:513px;top:393px;background:linear-gradient(135deg,#4a4a4a,#8a8f96 50%,#2c2c2c)" role="img" aria-label="Radio studio with hosts at the mixing desk"></div>
  <div class="abs show-title" style="left:514px;top:464px">Vestibulum Tempus Porta Libero</div>
  <p class="abs show-text" style="left:516px;top:481px">Curabitur congue lorem , quis ultrices nibh rhoncus vel. Nunc quis sapien et nisl ultrices suscipit sit amet tristique lorem. Nunc quis sapien suscipit tristique lorem.</p>
  <div class="abs more" style="left:634px;top:533px">More &nbsp;&nbsp; ▫</div>
  <div class="abs show-img" style="left:513px;top:561px;background:linear-gradient(135deg,#5a2a14,#b0562a 50%,#2a150c)" role="img" aria-label="Musicians playing guitar and fiddle on stage"></div>
  <div class="abs show-title" style="left:514px;top:632px">Vestibulum Tempus Porta Libero</div>
  <p class="abs show-text" style="left:516px;top:649px">Curabitur congue lorem , quis ultrices nibh rhoncus vel. Nunc quis sapien et nisl ultrices suscipit sit amet tristique lorem. Nunc quis sapien suscipit tristique lorem.</p>
  <div class="abs more" style="left:634px;top:701px">More &nbsp;&nbsp; ▫</div>
</aside>

<section class="past-shows">
  <div class="abs h2" style="left:84px;top:543px"><b>Past Shows</b></div>
  <div class="abs arrow-dot" style="left:474px;top:550px"></div>
  <div class="abs dotted" style="left:84px;top:567px;width:402px"></div>
  <div class="abs book" style="left:84px;top:582px;background:linear-gradient(#f4f4f4,#dfe6ee)" role="img" aria-label="Book cover with a globe"></div>
  <p class="abs past-text" style="left:173px;top:586px"><span class="lead">Marcus Delaney, former Editor-in-Chief of Circuit and author of Builders and The Wide Curve - See more at:</span> http://www.kellaway-ventures-example.com/#sthash.5imZfs7H.dpuf</p>
  <div class="abs past-btn" style="left:175px;top:689px">More &gt;&gt;</div>
  <div class="abs book" style="left:308px;top:586px;width:72px;height:94px;background:linear-gradient(135deg,#7fb0c0,#4d8799)" role="img" aria-label="Book cover with an orange leaf"></div>
  <p class="abs past-text" style="left:390px;top:586px"><span class="lead">Marcus Delaney, former Editor-in-Chief of Circuit and author of Builders and The Wide Curve - See more at:</span> http://www.kellaway-ventures-example.com/#sthash.5imZfs7H.dpuf</p>
  <div class="abs past-btn" style="left:391px;top:689px">More &gt;&gt;</div>
</section>

<section class="latest-blog">
  <div class="abs h2" style="left:84px;top:746px">Latest <b>Blog</b></div>
  <div class="abs arrow-dot" style="left:474px;top:753px"></div>
  <div class="abs dotted" style="left:84px;top:770px;width:402px"></div>

  <div class="abs blog-img" style="left:87px;top:786px;background:linear-gradient(135deg,#6b5a4a,#b89a7e 50%,#3c3430)" role="img" aria-label="Two hosts at studio microphones"></div>
  <div class="abs blog-title" style="left:249px;top:781px">Vestibulum tempus porta libero vitae suscipit. Praesent elit lorem, molestie</div>
  <div class="abs blog-by" style="left:249px;top:812px">by Marin Ostrova</div>
  <p class="abs blog-text" style="left:249px;top:824px">Morbi adipiscing, velit eu egestas bibendum, mauris risus ultricies nunc, eget dictum mi magna non eros. Quisque vel aliquet tellus. In hac habitasse platea dictumst.</p>
  <div class="abs share-btn" style="left:250px;top:859px;width:36px;background:var(--sky)">Tweet</div>
  <div class="abs share-count" style="left:290px;top:859px;width:10px">5</div>
  <div class="abs share-btn" style="left:308px;top:859px;width:38px;background:#4a67a8">Share</div>
  <div class="abs share-count" style="left:350px;top:859px;width:14px">52</div>
  <div class="abs more" style="left:457px;top:861px">More &gt;&gt;</div>

  <div class="abs blog-img" style="left:87px;top:900px;background:linear-gradient(135deg,#4a3a30,#a07a62 50%,#20406e)" role="img" aria-label="Host speaking into a studio microphone"></div>
  <div class="abs blog-title" style="left:249px;top:895px">Vestibulum tempus porta libero vitae suscipit. Praesent elit lorem, molestie</div>
  <div class="abs blog-by" style="left:249px;top:926px">by Marin Ostrova</div>
  <p class="abs blog-text" style="left:249px;top:938px">Morbi adipiscing, velit eu egestas bibendum, mauris risus ultricies nunc, eget dictum mi magna non eros. Quisque vel aliquet tellus. In hac habitasse platea dictumst.</p>
  <div class="abs share-btn" style="left:250px;top:973px;width:36px;background:var(--sky)">Tweet</div>
  <div class="abs share-count" style="left:290px;top:973px;width:10px">5</div>
  <div class="abs share-btn" style="left:308px;top:973px;width:38px;background:#4a67a8">Share</div>
  <div class="abs share-count" style="left:350px;top:973px;width:14px">52</div>
  <div class="abs more" style="left:457px;top:975px">More &gt;&gt;</div>
</section>

<aside class="latest-tweet">
  <div class="abs tweet-box"></div>
  <div class="abs tweet-head"><i></i>Latest Tweet</div>
  <div class="abs follow">Follow @Kellaway</div>
  <div class="abs followers">1,316 followers</div>

  <div class="abs avatar" style="top:802px;background:linear-gradient(#c9a070,#8a5a3a)" role="img" aria-label="Profile photo"></div>
  <div class="abs tweet" style="top:800px"><a>Kellaway @JessWinfield</a> Down stock market this morning. special, just a little down. &nbsp;&nbsp;<a>reply</a></div>
  <div class="abs avatar" style="top:848px;background:linear-gradient(#e0c090,#a8744a)" role="img" aria-label="Profile photo"></div>
  <div class="abs tweet" style="top:846px"><a>@HarlanOkafor</a> &nbsp;Down stock market this morning. Nothing special, just a little down. <a>reply</a></div>
  <div class="abs avatar" style="top:892px;background:linear-gradient(#c04050,#d8b090)" role="img" aria-label="Profile photo"></div>
  <div class="abs tweet" style="top:890px"><a>@HarlanOkafor</a> &nbsp;Down stock market this morning. Nothing special, just a little down. <a>reply</a></div>
  <div class="abs avatar" style="top:938px;background:linear-gradient(#e8c890,#b88058)" role="img" aria-label="Profile photo"></div>
  <div class="abs tweet" style="top:937px"><a>@HarlanOkafor</a> &nbsp;Down stock market this morning. Nothing special, just a little down. <a>reply</a></div>
  <div class="abs view-all">View All &gt;&gt;</div>
</aside>

<footer>
  <div class="abs foot-brand"><i></i>OrbitalWave</div>
  <div class="abs foot-social"><i></i><i></i><i></i><i></i><i></i><i></i></div>
  <div class="abs foot-text" style="top:1103px">Privacy Policy - Terms - FAQ</div>
  <div class="abs foot-text" style="top:1116px">© 2014 Kellaway Show, All Rights Reserved</div>
  <div class="abs foot-text" style="top:1129px">X2</div>
</footer>
</body>
</html>
```